The Brandwell Firm

We need a new design for our letterhead and envelopes. We are a personal injury and criminal defense firm so we need something modern and clean, but more on the professional/traditional side. Our new logo has two colors and is attached to the file so we need something that works well with those colors/matches the design. The following information needs to be on the letterhead:
Phone: (555) 214-3370
Fax: (555) 214-5186
Toll-Free: (888) 431-2059
Post Office Box 4721
Millbrook, SC 29555-4721
HarmClaimCounsel.example
PalmettoTrialAdvocates.example

Target Market(s)

Clients, government agencies, other law firms

Industry/Entity Type

Legal

Font styles to use
Sans Serif
Other font styles liked:
• Arial

Colors

Designer to choose colors to be used in the design.

Requirements
Must have
• Must look professional and clean, modern
Nice to have
• I would like to see a design that works with the logo but does not distract from the content that will be printed on it
Should not have
• Too many colors or crazy designs.

```html
<!DOCTYPE html>
<html lang="en">
<head>
<meta charset="utf-8">
<title>The Brandwell Firm — Stationery</title>
<link href="https://fonts.googleapis.com/css2?family=Open+Sans:wght@400;600&display=swap" rel="stylesheet">
<style>
  :root {
    --backdrop: #5a5a5c;
    --paper: #ffffff;
    --navy: #3c3d92;
    --flame: #d42a2a;
    --ink: #2b2b2b;
    --rule: #444444;
  }
  * { margin: 0; padding: 0; box-sizing: border-box; }
  html, body { width: 1200px; height: 904px; overflow: hidden; }
  body {
    position: relative;
    background: var(--backdrop);
    font-family: "Open Sans", Arial, sans-serif;
    color: var(--ink);
  }
  .sheet {
    position: absolute;
    background: var(--paper);
    box-shadow: 0 4px 14px rgba(0,0,0,.35);
  }
  .letterhead { left: 32px; top: 86px; width: 527px; height: 745px; }
  .envelope-front { left: 591px; top: 235px; width: 544px; height: 272px; }
  .envelope-back { left: 591px; top: 547px; width: 544px; height: 271px; overflow: hidden; }

  .brand {
    display: flex; align-items: center; gap: 7px;
    font-weight: 600; color: var(--navy); white-space: nowrap;
  }
  .brand-dot { width: 9px; height: 9px; border-radius: 50%; background: var(--flame); flex: none; }

  .letterhead .brand {
    position: absolute; top: 62px; left: 0; right: 0;
    justify-content: center; font-size: 19px;
  }
  .letter-footer {
    position: absolute; left: 36px; right: 35px; top: 709px;
    border-top: 1px solid var(--rule);
    padding-top: 7px;
    font-size: 8.3px; text-align: center; white-space: nowrap;
  }
  .letter-footer .icon { width: 8px; height: 8px; vertical-align: -1px; fill: var(--navy); }

  .envelope-front .brand { position: absolute; left: 31px; top: 60px; font-size: 16px; }
  .return-address {
    position: absolute; left: 53px; top: 102px;
    font-size: 8.5px; line-height: 12px; text-align: center;
  }

  .flap { position: absolute; left: 0; top: 0; }
  .envelope-back .brand {
    position: absolute; top: 36px; left: 0; right: 0;
    justify-content: center; font-size: 14px; color: var(--paper);
  }
  .envelope-back .brand-dot { background: var(--paper); width: 7px; height: 7px; }
</style>
</head>
<body>
  <svg width="0" height="0" style="position:absolute">
    <symbol id="phone" viewBox="0 0 10 10"><path d="M2 1 L4 1 L4.6 3 L3.4 3.8 Q4.4 5.8 6.2 6.6 L7 5.4 L9 6 L9 8 Q9 9 8 9 Q1 8.5 1 2 Q1 1 2 1Z"/></symbol>
    <symbol id="fax" viewBox="0 0 10 10"><rect x="3" y="1" width="4" height="3"/><rect x="1" y="4" width="8" height="4" rx="1"/><rect x="3" y="7" width="4" height="2.5" fill="#fff"/></symbol>
  </svg>

  <section class="sheet letterhead" aria-label="Letterhead">
    <div class="brand"><span class="brand-dot"></span>The Brandwell Firm</div>
    <footer class="letter-footer">
      Post Office Box 4721, Millbrook, SC 29555-4721 |
      <svg class="icon"><use href="#phone"/></svg> (555) 214-3370 |
      <svg class="icon"><use href="#fax"/></svg> (555) 214-5186 |
      <svg class="icon"><use href="#phone"/></svg> (888) 431-2059
    </footer>
  </section>

  <section class="sheet envelope-front" aria-label="Envelope front">
    <div class="brand"><span class="brand-dot"></span>The Brandwell Firm</div>
    <address class="return-address" style="font-style:normal">
      Post Office Box 4721<br>Millbrook, SC 29555-4721
    </address>
  </section>

  <section class="sheet envelope-back" aria-label="Envelope back">
    <svg class="flap" width="544" height="90" viewBox="0 0 544 90">
      <path d="M0 0 H544 V8 C544 38 528 48 496 50 L330 72 Q272 79 214 72 L48 50 C16 48 0 38 0 8 Z" fill="var(--navy)"/>
    </svg>
    <div class="brand"><span class="brand-dot"></span>The Brandwell Firm</div>
  </section>
</body>
</html>
```